4 Poster Designs required for Nail Salon

We require 4 poster designs that will be displayed inside a shopping centre. Each design should contain our logo and the words "Located next to Tallmart" (or similar). Design 1 (MOTHERS DAY) should contain the words "Mothers Day Special" and "$10 gift voucher when you spend over $50". Design 2 (CHRISTMAS) should contain the words "Christmas in July" and "Purchase a set of nails and get a $10 gift voucher". Design 3 (ALL YEAR) should contain the words "New Deluxe Spa Pedicure Service" and the words "Try our new Deluxe Spa Pedicure and get a free nail buff, shape and polish for your fingernails". Design 4 (ALL YEAR 2)should contain high quality nail salon image(s) and the words "Now Open". We like designs that support our image of high quality/fun/clean and safe.
Updates
I will close this early. In 24 hours.
Target Market(s)
Rich mums
Industry/Entity Type
Shopping
Look and feel
Each slider illustrates characteristics of the customer's brand and the style your logo design should communicate.

```html
<!DOCTYPE html>
<html lang="en">
<head>
<meta charset="utf-8">
<title>Christmas in July – Velvet Nail Salon</title>
<link rel="stylesheet" href="https://fonts.googleapis.com/css2?family=Cinzel+Decorative:wght@700;900&family=Playfair+Display:wght@700;900&family=Abril+Fatface&family=Anton&display=swap">
<style>
  :root{
    --magenta-deep:#b0107a;
    --magenta:#d6239a;
    --pink-glow:#f46cc4;
    --pink-soft:#fbd3ec;
    --snow:#ffffff;
    --offer-red:#c8102e;
    --brand-pink:#e0609f;
    --ink:#111111;
    --ring-warm:#d8305e;
    --ring-cool:#e86aa8;
    --gift-red:#c8102e;
    --gift-cream:#f3e9e2;
  }
  *{margin:0;padding:0;box-sizing:border-box}
  html,body{width:849px;height:1200px;overflow:hidden;background:var(--snow)}
  .poster{position:relative;width:849px;height:1200px;overflow:hidden;background:var(--snow)}
  .backdrop{position:absolute;inset:0}

  .title{position:absolute;left:0;top:0;width:100%;height:290px;font-family:"Cinzel Decorative",serif;font-weight:900;color:var(--snow)}
  .title span{position:absolute;white-space:nowrap;text-shadow:0 0 6px var(--pink-glow),0 0 14px var(--pink-glow),2px 3px 0 var(--magenta-deep)}
  .title-christmas{left:38px;top:30px;font-size:72px}
  .title-in{left:522px;top:188px;font-size:32px}
  .title-july{left:590px;top:160px;font-size:76px}

  .swatch-ring{position:absolute;left:143px;top:293px;width:560px;height:560px;border-radius:50%;
    background:radial-gradient(circle at 35% 30%,var(--ring-cool),var(--ring-warm) 70%,var(--magenta-deep))}
  .offer-disc{position:absolute;left:258px;top:408px;width:330px;height:330px;border-radius:50%;background:var(--snow)}

  .offer{position:absolute;left:258px;top:430px;width:330px;text-align:center;color:var(--offer-red)}
  .offer-lead{font-family:"Playfair Display",serif;font-weight:900;font-size:25px;line-height:1.15;text-transform:uppercase}
  .offer-amount{font-family:"Abril Fatface",serif;font-size:122px;line-height:1;margin-top:2px}
  .offer-tail{font-family:"Playfair Display",serif;font-weight:900;font-size:25px;text-transform:uppercase;margin-top:-4px}

  .brand{position:absolute;left:0;top:935px;width:100%;text-align:center;font-family:"Playfair Display",serif;font-weight:700;color:var(--brand-pink)}
  .brand-name{font-size:84px;line-height:1}
  .brand-sub{font-size:30px;margin-top:6px}

  .gift{position:absolute;top:1025px;width:70px;height:70px;border-radius:6px;
    background:linear-gradient(160deg,var(--gift-cream),#d9c9c0 60%,var(--gift-red))}
  .gift-left{left:22px}
  .gift-right{right:22px}

  .location{position:absolute;left:0;top:1122px;width:100%;text-align:center;font-family:"Anton",sans-serif;font-size:48px;line-height:1.1;color:var(--ink);letter-spacing:0.5px}
</style>
</head>
<body>
<main class="poster">
  <svg class="backdrop" width="849" height="1200" viewBox="0 0 849 1200" aria-hidden="true">
    <defs>
      <radialGradient id="skyGlow" cx="0.6" cy="0.4" r="0.8">
        <stop offset="0" stop-color="#f46cc4"/>
        <stop offset="0.5" stop-color="#d6239a"/>
        <stop offset="1" stop-color="#a80e72"/>
      </radialGradient>
      <linearGradient id="snowFade" x1="0" y1="0" x2="0" y2="1">
        <stop offset="0" stop-color="#fbd3ec"/>
        <stop offset="0.25" stop-color="#ffffff"/>
      </linearGradient>
    </defs>
    <rect class="sky" width="849" height="520" fill="url(#skyGlow)"/>
    <path class="snowdrift" d="M0 360 C90 320 170 380 260 350 C360 318 450 390 560 360 C660 332 760 380 849 345 L849 1200 L0 1200 Z" fill="url(#snowFade)"/>
  </svg>

  <h1 class="title" aria-label="Christmas in July">
    <span class="title-christmas">Christmas</span>
    <span class="title-in">in</span>
    <span class="title-july">July</span>
  </h1>

  <div class="swatch-ring" role="img" aria-label="Circle of colourful nail polish swatches"></div>
  <div class="offer-disc"></div>

  <section class="offer">
    <p class="offer-lead">Purchase<br>a set of nails<br>and get a</p>
    <p class="offer-amount">$10</p>
    <p class="offer-tail">Gift voucher</p>
  </section>

  <div class="brand">
    <p class="brand-name">Velvet</p>
    <p class="brand-sub">Nail Salon</p>
  </div>

  <div class="gift gift-left" role="img" aria-label="Wrapped Christmas gift box"></div>
  <div class="gift gift-right" role="img" aria-label="Wrapped Christmas gift box"></div>

  <p class="location">Located near to Tallmart</p>
</main>
</body>
</html>
```